Dog walking/Pet Sitting company needs a brochure to hook high end apartment tenants

We are looking for a brochure design that we can bring to meetings with high-end apartment and hotel management that will explain who we are, what we do, and how we can help their tenants/guests. I would like it to reflect the same look and feel of our website, carried over to printed brochure. Wesbite is www.hollowbrookpawcare.com. I can provide the stock images from the website if needed. A bi-fold brochure is ideal, unless you feel the information would fit better on a tri-fold. My company colors are #5D4664 and #5BA046. I would like a more professional tone to it, rather than fun.

Target Market(s)

Demo Professional Females and Males ages 30-50 with pets

Industry/Entity Type

Pet sitting

Font styles to use
Sans Serif

Colors
6b449b
9bcb3c

Requirements
Must have
• the same look and feel as my website; explain who we are, what we do, how we can help; include services offered; Mention that we service Parsippany and surrounding towns. Mention 15 years in business.
Should not have
• do not list pricing on brochure (you can mention pricing is available on the website). No cartoonish feel.

```html
<!DOCTYPE html>
<html lang="en">
<head>
<meta charset="utf-8">
<title>Hollowbrook Paw Care – Brochure Outside</title>
<link href="https://fonts.googleapis.com/css2?family=Source+Sans+3:ital,wght@0,400;0,600;0,700;1,400&display=swap" rel="stylesheet">
<style>
  :root {
    --plum: #5D4664;
    --plum-deep: #4f3b56;
    --leaf: #5BA046;
    --leaf-bright: #6cc04a;
    --ink-soft: #555;
    --paper: #ffffff;
    --stage: #ffffff;
  }
  * { box-sizing: border-box; margin: 0; padding: 0; }
  html, body { width: 1200px; height: 1200px; overflow: hidden; background: var(--stage); }
  body { position: relative; font-family: "Source Sans 3", sans-serif; }

  .brochure {
    position: absolute; left: 74px; top: 228px; width: 1052px; height: 742px;
    background: var(--paper);
    box-shadow: 0 10px 28px rgba(0,0,0,.22);
  }
  .panel-about {
    position: absolute; left: 0; top: 0; width: 578px; height: 742px;
    background: linear-gradient(90deg, var(--plum) 0%, var(--plum) 90%, var(--plum-deep) 100%);
    color: #fff;
  }
  .about-title {
    position: absolute; left: 42px; top: 40px;
    font-size: 23px; font-weight: 600; color: var(--leaf-bright);
  }
  .about-body {
    position: absolute; left: 42px; top: 84px; width: 417px;
    font-size: 10px; line-height: 13.5px; text-align: justify;
  }
  .about-body p { margin-bottom: 13.5px; }
  .signature { position: absolute; left: 42px; top: 476px; font-size: 11px; line-height: 14px; }
  .signature strong { font-weight: 700; display: block; }
  .signature em { font-size: 10px; }

  .dog-photo {
    position: absolute; left: 18px; top: 552px; width: 148px; height: 172px;
    border-radius: 40% 40% 12px 12px;
    background: radial-gradient(ellipse at 50% 35%, #c9a27a 0%, #8a5a3a 45%, rgba(93,70,100,0) 75%);
  }
  .contact {
    position: absolute; left: 166px; top: 620px; width: 300px; height: 81px;
    border-top: 1px solid rgba(255,255,255,.45);
    border-bottom: 1px solid rgba(255,255,255,.45);
  }
  .contact ul { list-style: none; position: absolute; left: 12px; top: 14px; }
  .contact li { display: flex; align-items: center; gap: 8px; font-size: 10.5px; line-height: 18px; }
  .contact li:first-child { font-size: 12px; font-weight: 600; }
  .contact svg { width: 11px; height: 11px; fill: var(--leaf-bright); flex: none; }

  .brand-small {
    position: absolute; left: 396px; top: 648px; display: flex; align-items: center; gap: 6px;
    font-size: 11px; font-weight: 600; color: #fff; width: 90px; line-height: 13px;
  }
  .brand-small .dot { width: 12px; height: 12px; border-radius: 50%; background: #fff; flex: none; }

  .arcs { position: absolute; left: 0; top: 0; width: 1200px; height: 1200px; pointer-events: none; }
  .hero-photo {
    position: absolute; left: 596px; top: 288px; width: 480px; height: 480px; border-radius: 50%;
    background: radial-gradient(circle at 55% 40%, #f1e6d6 0%, #d9c7ad 40%, #8c7d70 75%, #4a4046 100%);
  }
  .brand-badge {
    position: absolute; left: 922px; top: 262px; width: 160px; height: 160px; border-radius: 50%;
    background: var(--paper); border: 3px solid var(--plum);
    display: flex; align-items: center; justify-content: center; text-align: center;
    font-size: 19px; font-weight: 700; color: var(--plum); line-height: 22px; padding: 20px;
  }
  .tagline { position: absolute; left: 709px; top: 818px; }
  .tagline .lead { font-size: 22.5px; font-weight: 700; color: var(--plum); line-height: 29px; }
  .tagline .promise { font-size: 26px; font-weight: 700; color: var(--leaf); line-height: 34px; margin-top: 2px; }
  .tagline .url { font-size: 14px; font-weight: 600; color: var(--ink-soft); letter-spacing: 1.2px; margin-top: 12px; }

  .view-label {
    position: absolute; left: 0; top: 1080px; width: 1200px; text-align: center;
    font-size: 29px; color: #666; letter-spacing: .5px;
  }
</style>
</head>
<body>
  <div class="brochure">
    <section class="panel-about">
      <h2 class="about-title">About Us</h2>
      <div class="about-body">
        <p>We specialize in one-to-one personalized, quality pet care. We offer many services to cater to your needs. Whether you have dogs, cats, reptiles or rodents, we can help!</p>
        <p>Our business was born out of necessity. There were very few options for pet owners as recently as 15 years ago for pet care when pet owners needed to travel or work long hours. We were in the same boat, with a new puppy and both “mom and dad” working in an industry that took us away from our fur-baby for ten hours a day and business trips that didn’t allow an extra carry-on with fur sticking out! How would we ever find someone we trusted enough to care for our baby boy? Other pet owners must be resonating with these same feelings of guilt, worry and fear.</p>
        <p>I imagined a company that could provide peace of mind for pet owners. I knew that my vision would allow others to be able to enjoy the benefits of pet ownership, while maintaining their careers, social lives and family time without holding on to the guilt. I gave up my corporate career because of this belief. I wish I could say it was the hardest thing I have ever done, but in fact it was blissfully easy, because it was meant to be. I found my path and with a lot of hard work and long hours, my vision became a reality.</p>
        <p>Today, we are a fully-staffed company with employees (not independent contractors) who are as excited about working with pets as I am. We are continually educating ourselves and when we are not caring for pets, we are studying coursework on how to be better in-tune with dog behavior, pet health and related topics (we are a PawLearn Certified business). We truly pride ourselves on giving the pets we care for a full “experience” and not just a walk. The love I have seen from my staff warms my heart and gives me hope for this world!</p>
        <p>If you have pets and experience any feelings of guilt when you need to leave them behind, reach out to us! We pick right up where you leave off, with smiles, love and adventures that can turn an ordinary day extraordinary!</p>
      </div>
      <div class="signature"><strong>Dana Whitfield,</strong><em>Owner, Hollowbrook Paw Care LLC</em></div>

      <div class="dog-photo" role="img" aria-label="Photo of a small terrier lying down holding a leather leash in its mouth"></div>

      <div class="contact">
        <ul>
          <li><svg viewBox="0 0 24 24"><path d="M6.6 10.8a15.1 15.1 0 0 0 6.6 6.6l2.2-2.2c.3-.3.7-.4 1-.2 1.1.4 2.3.6 3.6.6.6 0 1 .4 1 1V20c0 .6-.4 1-1 1A17 17 0 0 1 3 4c0-.6.4-1 1-1h3.5c.6 0 1 .4 1 1 0 1.3.2 2.5.6 3.6.1.3 0 .7-.2 1z"/></svg>201-555-0148</li>
          <li><svg viewBox="0 0 24 24"><path d="M2 6h20v12H2zM2 6l10 7 10-7" fill="none" stroke="#6cc04a" stroke-width="2.4"/></svg>hello@hollowbrookpawcare.com</li>
          <li><svg viewBox="0 0 24 24"><circle cx="12" cy="12" r="9" fill="none" stroke="#6cc04a" stroke-width="2.2"/><path d="M3 12h18M12 3c3 3 3 15 0 18M12 3c-3 3-3 15 0 18" fill="none" stroke="#6cc04a" stroke-width="1.8"/></svg>www.hollowbrookpawcare.com</li>
        </ul>
      </div>
      <div class="brand-small"><span class="dot"></span><span>Hollowbrook Paw Care</span></div>
    </section>
  </div>

  <div class="hero-photo" role="img" aria-label="Photo of a smiling woman on a sofa hugging a brown and white spaniel"></div>

  <svg class="arcs" viewBox="0 0 1200 1200" aria-hidden="true">
    <path d="M905,286 A252 252 0 1 0 1073,442" fill="none" stroke="#5D4664" stroke-width="5"/>
    <path d="M743,272 A272 272 0 0 1 916,268" fill="none" stroke="#5BA046" stroke-width="3.5"/>
    <path d="M1086,422 A272 272 0 0 1 770,792" fill="none" stroke="#5BA046" stroke-width="3.5"/>
  </svg>

  <div class="brand-badge">Hollowbrook Paw Care</div>

  <div class="tagline">
    <p class="lead">Prioritize Your Family, Career,<br>Health, Social Life ,Goals,Yourself.</p>
    <p class="promise">We'll Focus on Your Pets.</p>
    <p class="url">www.hollowbrookpawcare.com</p>
  </div>

  <p class="view-label">Outside</p>
</body>
</html>
```